Roofing web site brvt roofing

Look at some of our competitors web page we like something similar with NYC roofing
https://www.quillbarroofing.example/
Maybe a skyline picture of nyc at the home page with a picture of flat roofing installation

Target Market(s)

Commercial and residential flat roofs

Industry/Entity Type

Flat Roofing industry

Coding

Coded - Design and coding required

Number of Pages Required

2 page

Font styles to use
Decorative
Script

Colors

Designer to choose colors to be used in the design.

Requirements
Must have
• At BRVT Roofing, we are a trusted and reputable roofing company specializing in new construction flat roof installation and repair. With years of experience in the industry, we take pride in providing exceptional roofing solutions to our valued clients. Our team of highly skilled and dedicated roofing professionals understands the unique challenges and requirements of new construction projects. We work closely with builders, contractors, and architects to design and install flat roofs that meet the specific needs of each project. From commercial buildings to residential complexes, we have the expertise to deliver reliable and durable roofing solutions. When it comes to flat roof repairs, we are your go-to experts. Our experienced technicians conduct thorough inspections to identify the root cause of any issues your roof may be experiencing. We utilize the latest industry techniques and high-quality materials to efficiently repair your flat roof, ensuring its integrity and longevity. At BRVT Roofing, we prioritize customer satisfaction above all else. We believe in building strong relationships with our clients by providing exceptional craftsmanship and outstanding customer service. Our team is dedicated to delivering projects on time, within budget, and to the highest standards of quality. We understand that a well-maintained roof is essential for protecting your property and ensuring the safety of its occupants. That's why we use only the best materials and employ skilled professionals who are trained in the latest roofing practices. Our commitment to excellence is evident in every project we undertake. As a fully licensed and insured roofing company, we prioritize safety and adhere to industry regulations and best practices. We take every precaution to create a safe working environment for our team and minimize any disruptions to your daily routine. When you choose BRVT Roofing, you can trust that you are working with a reliable and reputable company that will deliver exceptional results. We are committed to exceeding your expectations and providing you with a roof that is built to last. Contact us today for all your new construction flat roof installation and repair needs.
Nice to have
• NYC skyline background with commercial roofing pictures of torching roofing

```html
<!DOCTYPE html>
<html lang="en">
<head>
<meta charset="utf-8">
<title>Bravetta Roofing Co.</title>
<link href="https://fonts.googleapis.com/css2?family=Oswald:wght@400;500&family=Poppins:wght@400;500;600&display=swap" rel="stylesheet">
<style>
:root{
  --orange:#f26b30;
  --ink:#1c1c1c;
  --text:#444;
  --muted:#777;
  --soft:#f4f4f4;
  --line:#e6e6e6;
  --white:#fff;
  --dark:#141414;
}
*{box-sizing:border-box;margin:0;padding:0}
html,body{width:1200px;height:4252px;overflow:hidden}
body{position:relative;background:var(--white);font-family:'Poppins',sans-serif;color:var(--text)}
.abs{position:absolute}
.display{font-family:'Oswald',sans-serif;font-weight:500;color:var(--ink)}
.btn{position:absolute;background:var(--orange);color:var(--white);font-size:13px;font-weight:500;border-radius:22px;display:flex;align-items:center;justify-content:center}
.center{left:0;width:1200px;text-align:center}
.photo{position:absolute}

/* hero */
.hero{position:absolute;left:0;top:0;width:1200px;height:600px}
.brand{left:140px;top:32px;font-family:'Poppins',sans-serif;font-size:24px;font-weight:500;color:var(--white)}
.nav{top:36px;font-size:13px;color:var(--white);font-weight:500}
.hero-title{top:196px;font-size:46px;color:var(--white)}
.hero-sub{top:266px;font-size:16px;color:var(--white);font-weight:500}
.hero-list{font-size:13px;color:var(--white);font-weight:500}
.hero-list span::before{content:"•";margin-right:8px}
.hero-list span{margin:0 8px}

/* about */
.about-frame{left:142px;top:656px;width:412px;height:380px;background:var(--soft);border-radius:8px}
.about-title{left:619px;top:668px;font-size:38px;line-height:52px}
.about-copy{left:619px;width:440px;font-size:12.5px;line-height:22.5px;color:var(--text)}

/* services */
.section-title{font-size:36px}
.svc-circle{width:106px;height:106px;border-radius:50%;background:var(--orange)}
.svc-name{width:300px;text-align:center;font-size:22px;font-weight:500;color:var(--ink)}
.svc-text{width:280px;text-align:center;font-size:12px;line-height:22px;color:var(--text)}

/* reviews */
.review-card{left:221px;top:1683px;width:756px;height:238px;background:var(--soft);border-radius:8px}
.review-text{left:519px;top:1730px;width:432px;font-size:12.5px;line-height:22.5px}

/* why */
.why{left:553px;top:2033px;width:647px;height:572px;background:var(--orange)}
.why-title{left:599px;top:2110px;font-size:35px;color:var(--white)}
.why-item{left:647px;font-size:23px;color:var(--white)}
.why-icon{left:590px;width:36px;height:36px}

/* gallery */
.tile{top:2769px;width:208px;height:272px;border-radius:6px}

/* band */
.band{left:0;top:3185px;width:1200px;height:286px;background:linear-gradient(125deg,#0d0d0d 0%,#262626 45%,#0f0f0f 70%,#2a2a2a 100%)}

/* contact */
.contact-bg{left:0;top:3680px;width:1200px;height:572px;background:var(--soft)}
.card{top:3556px;width:211px;height:204px;background:var(--white);border-radius:8px;box-shadow:0 4px 18px rgba(0,0,0,.07);text-align:center}
.card h3{font-size:15px;font-weight:600;color:var(--ink);margin-top:8px}
.card p{font-size:12.5px;line-height:22px;color:var(--text);margin-top:8px}
.card svg{display:block;margin:0 auto}
.field-label{left:140px;font-size:15px;font-weight:600;color:var(--ink)}
.field-hint{left:141px;font-size:12px;color:var(--text)}
.field-line{left:140px;width:302px;height:1px;background:#888}
.touch-title{left:619px;top:3893px;font-family:'Oswald',sans-serif;font-size:36px;font-weight:500;color:var(--orange)}
.touch-copy{left:619px;top:3947px;width:440px;font-size:12.5px;line-height:22.5px;color:var(--text)}
.social{top:4027px;width:34px;height:34px;border-radius:50%;background:var(--orange)}
.foot-name{left:619px;top:4084px;font-family:'Poppins',sans-serif;font-size:24px;font-weight:500;color:#cbcbcb}
.footer{top:4198px;font-size:12px;color:var(--ink);font-weight:500}
</style>
</head>
<body>

<!-- hero -->
<svg class="hero" viewBox="0 0 1200 600" aria-hidden="true">
  <defs>
    <linearGradient id="sky" x1="0" y1="0" x2="0" y2="1">
      <stop offset="0" stop-color="#6b7d92"/>
      <stop offset="0.35" stop-color="#4a5a70"/>
      <stop offset="1" stop-color="#2a3850"/>
    </linearGradient>
  </defs>
  <path d="M0 480 Q600 640 1200 480 L1200 500 Q600 690 0 500 Z" fill="var(--orange)"/>
  <path d="M0 0 H1200 V482 Q600 642 0 482 Z" fill="url(#sky)"/>
</svg>
<div class="photo" role="img" aria-label="Flat commercial roof with city buildings and trees in the background" style="left:0;top:0;width:1200px;height:480px"></div>
<div class="abs brand">Bravetta Roofing Co.</div>
<div class="abs nav" style="left:757px">Home</div>
<div class="abs nav" style="left:840px;font-weight:400">Work Gallery</div>
<div class="btn" style="left:947px;top:28px;width:114px;height:36px">Contact Us</div>
<div class="abs center display hero-title">Flat Roof Specialists</div>
<div class="abs center hero-sub">Flat Roof Installation, Repair &amp; Restoration Specialists For:</div>
<div class="abs center hero-list" style="top:300px"><span style="font-size:14px">Commercial</span><span>Real Estate Management</span><span style="font-size:14px">Business</span></div>
<div class="abs center hero-list" style="top:323px"><span style="font-size:14px">Schools</span><span>Warehouses</span></div>
<div class="btn" style="left:543px;top:366px;width:114px;height:36px">Contact Us</div>

<!-- about -->
<div class="abs about-frame"></div>
<div class="photo" role="img" aria-label="Roofer torching a membrane roll onto a flat roof" style="left:157px;top:672px;width:412px;height:364px;border-radius:8px;background:linear-gradient(160deg,#cfd6df 0%,#8b97a6 40%,#3a4f86 70%,#6b7080 100%)"></div>
<div class="abs display about-title">About Bravetta Roofing Co.<br>Of New York</div>
<div class="abs about-copy" style="top:783px">Marcus Brought Together The Best In The Business To Create His Dream. Though He Takes Pride In All Aspects Of Roofing, Working And Living On The Coast Has Lead To A Passion For Quick, Efficient, And Transparent Repairs To Storm Damaged Homes.</div>
<div class="abs about-copy" style="top:884px">Lorem Ipsum Is Simply Dummy Text Of The Printing And Typesetting Industry. Lorem Ipsum Has Been The Industry's Standard Dummy Text Ever Since The To Same &nbsp;1500S, When An Unknown Printer Took A Galley Of Type And Scrambled It To Type Specimen Book.</div>
<div class="btn" style="left:619px;top:990px;width:124px;height:36px">Contact Us</div>

<!-- services -->
<div class="abs center display section-title" style="top:1112px">Our Services</div>
<div class="abs svc-circle" style="left:219px;top:1220px"></div>
<svg class="abs" style="left:242px;top:1243px" width="60" height="60" viewBox="0 0 60 60" fill="none" stroke="#fff" stroke-width="2"><path d="M6 36 L30 14 L54 36"/><path d="M14 30 V50 H46 V30"/><circle cx="38" cy="18" r="9"/><path d="M24 40 H36 M24 45 H36"/></svg>
<div class="abs svc-circle" style="left:533px;top:1220px"></div>
<svg class="abs" style="left:556px;top:1243px" width="60" height="60" viewBox="0 0 60 60" fill="none" stroke="#fff" stroke-width="2"><path d="M12 14 H48 L52 46 H8 Z"/><path d="M10 26 H50 M9 36 H51 M24 14 L22 46 M36 14 L38 46"/></svg>
<div class="abs svc-circle" style="left:861px;top:1220px"></div>
<svg class="abs" style="left:884px;top:1243px" width="60" height="60" viewBox="0 0 60 60" fill="none" stroke="#fff" stroke-width="2"><path d="M16 24 Q26 8 36 24 Z"/><circle cx="26" cy="32" r="7"/><path d="M12 52 Q12 40 26 40 Q40 40 40 52"/><path d="M46 30 Q52 40 46 44 Q40 40 46 30 Z"/></svg>
<div class="abs svc-name" style="left:122px;top:1344px">Roof Leak Repairs</div>
<div class="abs svc-text" style="left:132px;top:1382px">Flat Roofing Maintenance Includes Drain- Ing Water, Repairing Your Roof's Infiltration System, And Getting Rid Of</div>
<div class="abs svc-name" style="left:443px;top:1344px">Flashing Services</div>
<div class="abs svc-text" style="left:453px;top:1382px">Roof Flashing Plays An Important Role In Leak Prevention At The Most Vulnerable Areas Of Your Roof</div>
<div class="abs svc-name" style="left:772px;top:1344px">Waterproofing Experts</div>
<div class="abs svc-text" style="left:782px;top:1382px">Our Highly-Skilled Technicians Will Expertly Diagnose Your Problem Areas And Provide You Solution To Your Specific Need.</div>
<div class="btn" style="left:543px;top:1472px;width:114px;height:34px">Contact Us</div>

<!-- reviews -->
<div class="abs center display section-title" style="top:1582px">Client Reviews</div>
<div class="abs review-card"></div>
<div class="photo" role="img" aria-label="Portrait of a smiling client" style="left:252px;top:1665px;width:222px;height:274px;border-radius:8px;background:linear-gradient(180deg,#e4e4e4 0%,#d8d2cc 55%,#b8584d 100%)"></div>
<div class="abs review-text">Lorem Ipsum Is Simply Dummy Text Of The Printing And Typesetting Industry. Lorem Ipsum Has Been The Industry's Standard Dummy Text Ever Since The 1500S, When An Unknown Printer Took A Galley Of Type And Scrambled It To Make A Type Specimen Book.</div>
<div class="abs" style="left:519px;top:1834px;font-size:13px;font-weight:600;color:var(--ink)">Daniel Morrow</div>
<svg class="abs" style="left:519px;top:1856px" width="72" height="14" viewBox="0 0 72 14" fill="#f5b400"><g id="st"><path d="M7 0 L9 5 L14 5 L10 8 L11.5 13 L7 10 L2.5 13 L4 8 L0 5 L5 5 Z"/></g><use href="#st" x="14"/><use href="#st" x="28"/><use href="#st" x="42"/><use href="#st" x="56"/></svg>
<svg class="abs" style="left:893px;top:1836px" width="46" height="36" viewBox="0 0 46 36" fill="var(--orange)"><path d="M2 2 H20 V20 Q20 32 6 35 L4 30 Q12 27 12 20 H2 Z"/><path d="M26 2 H44 V20 Q44 32 30 35 L28 30 Q36 27 36 20 H26 Z"/></svg>
<svg class="abs" style="left:171px;top:1787px" width="30" height="30" viewBox="0 0 30 30" fill="none" stroke="var(--ink)" stroke-width="1.8"><circle cx="15" cy="15" r="13.5"/><path d="M21 15 H9 M14 10 L9 15 L14 20"/></svg>
<svg class="abs" style="left:998px;top:1787px" width="30" height="30" viewBox="0 0 30 30" fill="none" stroke="var(--ink)" stroke-width="1.8"><circle cx="15" cy="15" r="13.5"/><path d="M9 15 H21 M16 10 L21 15 L16 20"/></svg>

<!-- why choose us -->
<div class="photo" role="img" aria-label="Worker pressure-washing a clay tile roof with a skylight" style="left:0;top:2033px;width:553px;height:572px;background:linear-gradient(150deg,#7a8090 0%,#c46a45 30%,#a8472a 60%,#6e2e1d 100%)"></div>
<div class="abs why"></div>
<div class="abs why-title">Why Choose Us</div>
<svg class="abs why-icon" style="top:2177px" viewBox="0 0 36 36" fill="none" stroke="#fff" stroke-width="1.6"><circle cx="18" cy="14" r="10"/><circle cx="18" cy="14" r="5"/><path d="M12 22 L10 34 L18 29 L26 34 L24 22"/></svg>
<div class="abs why-item" style="top:2180px">Licensed, Bonded, &amp; Insured</div>
<svg class="abs why-icon" style="top:2244px" viewBox="0 0 36 36" fill="none" stroke="#fff" stroke-width="1.6"><rect x="4" y="10" width="28" height="22" rx="2"/><path d="M12 10 V5 H24 V10 M4 18 H32"/></svg>
<div class="abs why-item" style="top:2246px">Reliable &amp; Experienced Professionals</div>
<svg class="abs why-icon" style="top:2312px" viewBox="0 0 36 36" fill="none" stroke="#fff" stroke-width="1.6"><rect x="6" y="4" width="20" height="28" rx="2"/><path d="M11 12 H21 M11 18 H21 M11 24 H16"/><circle cx="26" cy="26" r="6"/><path d="M30 30 L34 34"/></svg>
<div class="abs why-item" style="top:2314px">Free Evaluations &amp; Estimates</div>
<svg class="abs why-icon" style="top:2370px" viewBox="0 0 36 36" fill="none" stroke="#fff" stroke-width="1.6"><path d="M18 4 Q28 14 18 24 Q8 14 18 4 Z"/><path d="M4 32 Q10 24 18 28 Q26 24 32 32"/></svg>
<div class="abs why-item" style="top:2372px">Lead-Safe Certified</div>
<svg class="abs why-icon" style="top:2431px" viewBox="0 0 36 36" fill="none" stroke="#fff" stroke-width="1.6"><circle cx="18" cy="18" r="14"/><text x="18" y="23" text-anchor="middle" font-size="12" fill="#fff" stroke="none" font-family="Poppins, sans-serif">24</text></svg>
<div class="abs why-item" style="top:2433px">24/7 Emergency Response</div>
<div class="btn" style="left:590px;top:2490px;width:128px;height:34px;background:#fff;color:var(--orange)">Contact Us</div>

<!-- gallery -->
<div class="abs center display section-title" style="top:2684px">Work Gallery</div>
<div class="photo tile" role="img" aria-label="Roofers applying membrane to a flat roof" style="left:140px;background:linear-gradient(170deg,#7a7f85 0%,#3f5d8f 60%,#1f3c74 100%)"></div>
<div class="photo tile" role="img" aria-label="Worker spreading coating on a roof" style="left:378px;background:linear-gradient(170deg,#5e5e5e 0%,#cfd3d6 55%,#b9bdc1 100%)"></div>
<div class="photo tile" role="img" aria-label="Gloved hands fitting roof flashing" style="left:614px;background:linear-gradient(170deg,#7c8a5a 0%,#b23a3a 35%,#6a5a58 70%,#4a4040 100%)"></div>
<div class="photo tile" role="img" aria-label="Roofer installing shingles" style="left:850px;background:linear-gradient(170deg,#8a8a8a 0%,#e08540 40%,#4e4e52 100%)"></div>
<div class="btn" style="left:543px;top:3066px;width:114px;height:34px">See All</div>

<!-- projects band -->
<div class="abs band"></div>
<div class="abs center" style="top:3265px;font-size:15px;color:#fff">See What We've Been Working On...</div>
<div class="abs center display" style="top:3290px;font-size:36px;color:#fff">View Some Of Our Latest Projects</div>
<div class="btn" style="left:535px;top:3356px;width:130px;height:34px">View Projects</div>

<!-- contact -->
<div class="abs contact-bg"></div>
<div class="abs card" style="left:155px;padding-top:54px">
  <svg width="28" height="32" viewBox="0 0 28 32" fill="none" stroke="var(--orange)" stroke-width="1.6"><path d="M14 30 Q3 18 3 12 A11 11 0 0 1 25 12 Q25 18 14 30 Z"/><circle cx="14" cy="12" r="4"/></svg>
  <h3>Our Office</h3><p>123, Building Name, Street,<br>City, State AB 123456</p>
</div>
<div class="abs card" style="left:381px;padding-top:54px">
  <svg width="28" height="28" viewBox="0 0 28 28" fill="none" stroke="var(--orange)" stroke-width="1.6"><path d="M6 3 L11 3 L13 9 L10 11 Q13 17 17 18 L19 15 L25 17 L25 22 Q24 25 20 25 Q5 22 3 7 Q3 3 6 3 Z"/></svg>
  <h3>Phone Number</h3><p>123 456 7890</p>
</div>
<div class="abs card" style="left:607px;padding-top:58px">
  <svg width="28" height="22" viewBox="0 0 28 22" fill="none" stroke="var(--orange)" stroke-width="1.6"><rect x="2" y="2" width="24" height="18" rx="1"/><path d="M2 3 L14 13 L26 3"/></svg>
  <h3>Email</h3><p style="font-size:12px">brvtroofing@mailbox.example</p>
</div>
<div class="abs card" style="left:833px;padding-top:54px">
  <svg width="34" height="30" viewBox="0 0 34 30" fill="none" stroke="var(--orange)" stroke-width="1.6"><path d="M4 14 A12 10 0 1 1 10 23 L4 27 Z"/><circle cx="11" cy="14" r="1.2"/><circle cx="17" cy="14" r="1.2"/><circle cx="23" cy="14" r="1.2"/></svg>
  <h3>Chat</h3><p>24/7 Emergency Support</p>
</div>

<div class="abs field-label" style="top:3835px">Email</div>
<div class="abs field-hint" style="top:3868px">Enter Valid Email Address</div>
<div class="abs field-line" style="top:3894px"></div>
<div class="abs field-label" style="top:3912px">Name</div>
<div class="abs field-hint" style="top:3945px">Enter Your Name</div>
<div class="abs field-line" style="top:3971px"></div>
<div class="abs field-label" style="top:3989px">Message</div>
<div class="abs field-hint" style="top:4022px">Enter Your Message</div>
<div class="abs field-line" style="top:4108px"></div>
<div class="btn" style="left:140px;top:4128px;width:302px;height:34px">Submit</div>

<div class="abs touch-title">Get In Touch</div>
<div class="abs touch-copy">We stay in constant communication with our customers until the job is done. To get a free quote, or if you have questions or special requests, just drop us a line.</div>
<div class="abs social" style="left:619px" role="img" aria-label="Social profile"></div>
<div class="abs social" style="left:676px" role="img" aria-label="Social profile"></div>
<div class="abs social" style="left:733px" role="img" aria-label="Social profile"></div>
<div class="abs foot-name">Bravetta Roofing Co.</div>

<div class="abs center footer">© &nbsp;2024 Bravetta Roofing Co. All Rights Reserved</div>

</body>
</html>
```